2 sided postcard for New Internet Customers

We would like a design for a two sided postcard (with room for mailing label), dimensions 9 1/4 by 6 1/4 to be sent via US Mail.

The postcard needs to include our logo (attached) and the text
Fiber Optic Internet
555-318-2094
http://www.brightmesh.example
Speeds up to 1 Gig, with packages starting at $55

These will be sent to people who do not have our service.

Since this is going to be "junk mail" we probably only have 1 second or less to capture someone's attention to encourage them to read the entire postcard.

We are a "mom and pop" telecommunications company that provides internet, phone, and television services on the fiber optic network that we designed, built, and maintain.

We started as a dial up ISP in 1995, and have extraordinary technical support based in Freeport PA, our customers actually get the speeds they pay for, and our service is highly reliable.

We have a slogan (which you can choose to use or ignore) which is
"I Got Zoomed with Pellworth"

Existing customers can earn a $50 credit for every new customer they refer to us. Unlike most large cable and internet companies we have very happy customers... some who have stayed with us for decades.

I've attached our previous postcard, which I really dislike. It does have a blank spot for where the mailing label should go.

Target Market(s)

New Internet Customers in Western Pennsylvania

Industry/Entity Type

Internet

Font styles to use
Other font styles liked:
• Just match our logo.

Colors

Designer to choose colors to be used in the design.

Requirements
Must have
• The postcard needs to include our logo, and the text Fiber Optic Internet 555-318-2094 http://www.brightmesh.example Speeds up to 1 Gig, with packages starting at $55
Nice to have
• The colors and fonts should look good with our logo.
Should not have
• Should not have small print or lots of text. Both sides need to capture attention.

```html
<!DOCTYPE html>
<html lang="en">
<head>
<meta charset="utf-8">
<title>Pellworth Fiber Postcard</title>
<link rel="stylesheet" href="https://fonts.googleapis.com/css2?family=Archivo:ital,wdth,wght@0,125,900;1,125,900&family=Oswald:wght@400;500&family=Poppins:ital,wght@0,400;0,600;1,400;1,600;1,700&display=swap">
<style>
:root{
  --page:#e2e2e2;
  --navy:#0b0d3a;
  --deep:#05061a;
  --blue:#0a6fc9;
  --blue-bright:#1e9be8;
  --red:#d3141c;
  --yellow:#ffd200;
  --white:#ffffff;
  --stamp:#e6e6e6;
}
*{margin:0;padding:0;box-sizing:border-box}
html,body{width:706px;height:1200px;overflow:hidden;background:var(--page)}
.canvas{position:relative;width:706px;height:1200px}
.card{position:absolute;left:33px;width:640px;height:427px;overflow:hidden;box-shadow:4px 6px 10px rgba(0,0,0,.35)}
.front{top:140px;background:radial-gradient(ellipse at 75% 30%,#22208a 0%,var(--navy) 45%,var(--deep) 100%)}
.back{top:620px;background:var(--white)}
.abs{position:absolute}
.wide{font-family:"Archivo",sans-serif;font-stretch:125%;font-weight:900;text-transform:uppercase;line-height:.9}
.body-text{font-family:"Poppins",sans-serif}
.cond{font-family:"Oswald",sans-serif}

/* brand */
.brand{display:flex;flex-direction:column;align-items:flex-start}
.brand-row{display:flex;align-items:center;gap:6px}
.brand-dot{width:34px;height:34px;border-radius:50%;background:var(--blue-bright)}
.brand-name{font-family:"Poppins",sans-serif;font-size:14px;line-height:1.05}
.brand-name small{display:block;font-size:7px}
.brand-tag{margin-top:3px;background:var(--blue);color:var(--white);font-family:"Poppins",sans-serif;font-style:italic;font-size:13px;padding:0 4px;line-height:18px}
.front .brand-name{color:var(--white)}
.back .brand-name{color:#222}

/* front */
.hero-photo{left:330px;top:0;width:310px;height:427px;background:radial-gradient(ellipse at 60% 40%,#2f8cff 0%,#1b3fc0 30%,#151a6a 60%,transparent 85%)}
.headline-1{left:32px;top:106px;font-size:34px;color:var(--white);font-style:italic;letter-spacing:.5px}
.headline-2{left:32px;top:136px;font-size:46px;font-style:italic;color:var(--blue-bright);letter-spacing:.5px}
.intro{left:45px;top:186px;width:310px;font-size:10px;line-height:1.2;color:var(--white)}
.intro::before{content:"";position:absolute;left:-10px;top:4px;width:3px;height:28px;background:var(--red);transform:skewX(-12deg)}
.speed-band{left:0;top:241px;width:384px;height:34px;background:var(--red);clip-path:polygon(0 0,100% 0,97% 100%,0 100%);color:var(--white)}
.speed-band .lbl{position:absolute;font-size:10.5px;line-height:.9}
.speed-band .big{position:absolute;font-size:24px;font-style:italic}
.speed-band .start{position:absolute;left:307px;top:3px;font-family:"Poppins",sans-serif;font-size:7px;letter-spacing:2px}
.price-band{left:0;top:275px;width:344px;height:67px;background:linear-gradient(90deg,var(--blue),#0a5cb0);clip-path:polygon(0 0,100% 0,97% 100%,0 100%);display:flex}
.price{flex:1;padding:12px 0 0 30px;color:var(--white);position:relative}
.price+.price{border-left:0}
.price:nth-child(2){background:rgba(0,0,0,.12);clip-path:polygon(4% 0,100% 0,96% 100%,0 100%)}
.price h3{font-family:"Poppins",sans-serif;font-style:italic;font-weight:700;font-size:6.5px;line-height:1.1;text-transform:uppercase}
.price span{display:inline-block;margin-top:3px;background:var(--deep);border-radius:6px;font-family:"Poppins",sans-serif;font-style:italic;font-size:5.5px;padding:1px 8px}
.price b{display:block;margin-top:3px;font-size:13px;color:var(--yellow);font-style:italic}
.slogan{left:463px;top:188px;width:104px;height:98px;background:var(--red);border-radius:6px;transform:rotate(6deg);display:flex;align-items:center;justify-content:center;text-align:center;color:var(--white);font-size:19px;line-height:.95;text-transform:uppercase;box-shadow:0 0 12px rgba(0,0,0,.5)}
.phone-line{display:flex;align-items:center;gap:5px;color:var(--white)}
.phone-line svg{width:15px;height:15px}
.front .phone-line{left:31px;top:366px;font-size:27px}
.divider{left:278px;top:368px;width:1px;height:28px;background:rgba(255,255,255,.5)}
.credit{color:var(--white)}
.credit .lbl{position:absolute;font-size:8.5px;line-height:.85}
.credit .amt{position:absolute;color:var(--yellow);font-size:15px;font-style:italic;line-height:.9}
.credit .note{position:absolute;font-family:"Poppins",sans-serif;font-style:italic;text-transform:uppercase;white-space:nowrap}
.front .credit{left:245px;top:368px}
.web-bar{left:445px;top:378px;width:195px;height:20px;background:var(--blue);clip-path:polygon(2% 0,100% 0,100% 100%,0 100%);color:var(--white);font-family:"Poppins",sans-serif;font-weight:600;font-size:10px;letter-spacing:1.5px;line-height:20px;padding-left:14px}

/* back */
.back-panel{left:0;top:0;width:332px;height:427px;background:linear-gradient(180deg,var(--deep) 0%,var(--navy) 50%,#1a1c5a 70%);clip-path:polygon(0 0,100% 0,85% 100%,0 100%)}
.city-photo{left:0;top:300px;width:300px;height:127px;background:linear-gradient(180deg,transparent 0%,#1d2a4a 40%,#5a4a2a 80%,#2a2a3a 100%);clip-path:polygon(0 0,100% 0,97% 100%,0 100%)}
.mom-1{left:36px;top:38px;font-size:14px;color:var(--white);font-style:italic}
.mom-2{left:36px;top:53px;font-size:19px;color:var(--blue-bright);font-style:italic}
.mom-sub{left:37px;top:75px;font-size:8px;color:var(--red);font-weight:600;font-style:italic;text-transform:uppercase}
.mom-text{left:37px;top:92px;width:230px;font-size:9px;line-height:1.3;color:var(--white)}
.ref-band{left:0;top:152px;width:329px;height:63px;background:var(--blue);clip-path:polygon(0 0,100% 0,98% 100%,0 100%)}
.back .credit{left:37px;top:158px}
.provide{left:38px;top:240px;font-size:17px;color:var(--white);font-style:italic}
.provide-sub{left:38px;top:256px;font-family:"Poppins",sans-serif;font-weight:600;font-style:italic;font-size:9px;letter-spacing:3px;color:var(--yellow)}
.service{width:62px;height:62px;top:277px;border-radius:50%;background:var(--red);border:3px solid rgba(120,20,30,.7);color:var(--white);display:flex;flex-direction:column;align-items:center;justify-content:center;text-align:center;font-family:"Poppins",sans-serif;font-weight:700;font-style:italic;font-size:7px;line-height:1.05}
.service svg{width:16px;height:16px;margin-bottom:2px}
.stamp{left:551px;top:36px;width:55px;height:72px;background:var(--stamp)}
.back .phone-line{left:311px;top:383px;font-size:18px;color:#222}
.back .phone-line svg{width:13px;height:13px}
</style>
</head>
<body>
<main class="canvas">

  <!-- FRONT -->
  <section class="card front">
    <div class="abs hero-photo" role="img" aria-label="Hand holding a glowing smartphone with a bundle of bright fiber optic strands bursting from the screen"></div>

    <div class="abs brand" style="left:34px;top:31px">
      <div class="brand-row">
        <span class="brand-dot"></span>
        <span class="brand-name">Pellworth, Inc.<small>www.pellworth.example</small></span>
      </div>
      <span class="brand-tag">Internet Services</span>
    </div>

    <h1 class="abs wide headline-1">Fiber Optic</h1>
    <h1 class="abs wide headline-2">Internet</h1>
    <p class="abs body-text intro">Pellworth outperforms other local Internet and phone service providers by delivering Internet and phone service over the newest, most reliable communications network - Fiber Optics!</p>

    <div class="abs speed-band wide">
      <span class="lbl" style="left:33px;top:7px">Speeds<br>up to</span>
      <span class="big" style="left:107px;top:5px">1 Gig</span>
      <span class="lbl" style="left:202px;top:7px">With<br>packages</span>
      <span class="start">STARTING AT</span>
      <span class="big" style="left:305px;top:12px;font-size:20px">$55</span>
    </div>

    <div class="abs price-band">
      <div class="price"><h3>High speed<br>internet service</h3><span>25mbps download</span><b class="wide">$55/mo</b></div>
      <div class="price"><h3>VoIP phone<br>service</h3><span>10mbps download</span><b class="wide">$25/mo</b></div>
      <div class="price"><h3>Phone &amp; internet<br>packages</h3><span>10mbps download</span><b class="wide">$80/mo</b></div>
    </div>

    <div class="abs cond slogan">I Got Zoomed<br>with<br>Pellworth</div>

    <div class="abs phone-line cond">
      <svg viewBox="0 0 24 24"><circle cx="12" cy="12" r="12" fill="#d3141c"/><path d="M8 6l2 3-1.3 1.4a8 8 0 0 0 4.9 4.9L15 14l3 2-1.2 2.2C11 18 6 13 5.8 7.2z" fill="#fff"/></svg>
      <span>(555) 318-2094</span>
    </div>
    <div class="abs divider"></div>
    <div class="abs credit wide">
      <span class="lbl" style="left:0;top:2px">Existing<br>customers<br>can earn a</span>
      <span class="amt" style="left:65px;top:0">$50<br>credit</span>
      <span class="note" style="left:0;top:28px;font-size:6.5px;color:var(--red)">For every new customer they refer to us</span>
    </div>
    <div class="abs web-bar">www.brightmesh.example</div>
  </section>

  <!-- BACK -->
  <section class="card back">
    <div class="abs back-panel"></div>
    <div class="abs city-photo" role="img" aria-label="Night city skyline with glowing network connection lines"></div>

    <h2 class="abs wide mom-1">We are a</h2>
    <h2 class="abs wide mom-2">"Mom and Pop"</h2>
    <p class="abs body-text mom-sub">Telecommunications company</p>
    <p class="abs body-text mom-text">that provides internet, phone, and television services on the fiber optic network that we designed, built, and maintain.</p>

    <div class="abs ref-band"></div>
    <div class="abs credit wide">
      <span class="lbl" style="left:0;top:3px;font-size:11px">Existing<br>customers<br>can earn a</span>
      <span class="amt" style="left:121px;top:0;font-size:19px">$50<br>credit</span>
      <span class="note" style="left:0;top:42px;font-size:8px;font-style:normal">For every new customer they refer to us</span>
    </div>

    <h2 class="abs wide provide">We provide</h2>
    <p class="abs provide-sub">FOR RESIDENTIAL &amp; BUSINESS</p>

    <div class="abs service" style="left:38px">
      <svg viewBox="0 0 24 24" fill="none" stroke="#ffd200" stroke-width="2.2" stroke-linecap="round"><path d="M3 9a13 13 0 0 1 18 0M6 12.5a8.5 8.5 0 0 1 12 0M9 16a4 4 0 0 1 6 0"/><circle cx="12" cy="19" r="1.3" fill="#ffd200"/></svg>
      Internet<br>Service
    </div>
    <div class="abs service" style="left:122px">
      <svg viewBox="0 0 24 24" fill="none" stroke="#ffd200" stroke-width="2"><rect x="7" y="2" width="10" height="20" rx="2"/><path d="M11 18.5h2"/></svg>
      Phone<br>Service
    </div>
    <div class="abs service" style="left:205px">
      <svg viewBox="0 0 24 24" fill="none" stroke="#ffd200" stroke-width="2"><rect x="8" y="4" width="9" height="16" rx="2"/><path d="M4 7a6 6 0 0 1 3-4M2 10a10 10 0 0 1 4-8"/></svg>
      Internet &amp;<br>Phone<br>Packages
    </div>

    <div class="abs brand" style="left:358px;top:36px">
      <div class="brand-row">
        <span class="brand-dot" style="width:26px;height:26px"></span>
        <span class="brand-name" style="font-size:12px">Pellworth, Inc.<small>www.pellworth.example</small></span>
      </div>
      <span class="brand-tag" style="font-size:11px;line-height:14px">Internet Services</span>
    </div>
    <div class="abs stamp"></div>

    <div class="abs phone-line cond">
      <svg viewBox="0 0 24 24"><circle cx="12" cy="12" r="12" fill="#d3141c"/><path d="M8 6l2 3-1.3 1.4a8 8 0 0 0 4.9 4.9L15 14l3 2-1.2 2.2C11 18 6 13 5.8 7.2z" fill="#fff"/></svg>
      <span>(555) 318-2094</span>
    </div>
    <div class="abs web-bar">www.brightmesh.example</div>
  </section>

</main>
</body>
</html>
```